Realty Group Needs Classy, Contemporary Letterhead Design

We need a letterhead design for a new realty company located in NY, USA. We buy investment properties to rehabilitate and or keep in our rental portfolio.

```html
<!DOCTYPE html>
<html lang="en">
<head>
<meta charset="utf-8">
<title>Halvorsen Realty Group – Letterhead</title>
<link href="https://fonts.googleapis.com/css2?family=Open+Sans:wght@400;600;700;800&display=swap" rel="stylesheet">
<style>
  :root {
    --purple: #4b2a91;
    --purple-dark: #3d2178;
    --grey: #8c8c8c;
    --ink: #2b2b2b;
    --body: #4a4a4a;
    --backdrop: #e9e9ea;
    --paper: #ffffff;
  }
  * { box-sizing: border-box; margin: 0; padding: 0; }
  html, body {
    width: 1200px; height: 795px; overflow: hidden;
    background: var(--backdrop);
    font-family: "Open Sans", Arial, sans-serif;
  }
  .letterhead {
    position: absolute; left: 333px; top: 20px;
    width: 534px; height: 755px;
    background: var(--paper);
    box-shadow: 0 2px 10px rgba(0,0,0,.12);
    overflow: hidden;
  }
  .brand {
    position: absolute; left: 44px; top: 46px;
    display: flex; align-items: center; gap: 8px;
    color: var(--purple); font-weight: 800;
  }
  .brand-mark { width: 12px; height: 12px; border-radius: 50%; background: var(--purple); }
  .brand-name { font-size: 22px; letter-spacing: .5px; line-height: 1; }
  .brand-sub { font-size: 8px; letter-spacing: 1.5px; margin-top: 2px; text-transform: uppercase; }
  .letter {
    position: absolute; left: 44px; top: 178px; width: 446px;
    font-size: 8.6px; line-height: 1.45; color: var(--body);
  }
  .date, .recipient { color: var(--ink); font-size: 9px; }
  .date { margin-bottom: 10px; }
  .recipient { margin-bottom: 12px; }
  .salutation { font-weight: 700; color: var(--ink); font-size: 9.5px; margin-bottom: 12px; }
  .letter p.copy { margin-bottom: 11px; text-align: justify; }
  .closing { margin-top: 18px; color: var(--ink); font-size: 9px; }
  .signature {
    margin-top: 8px; width: 90px; height: 30px;
    background: linear-gradient(90deg, #f1f1f3, #e4e4e8);
    border-radius: 3px;
  }
  .footer { position: absolute; left: 0; bottom: 0; width: 534px; height: 170px; }
  .footer svg { position: absolute; inset: 0; }
  .office-address {
    position: absolute; left: 20px; bottom: 12px;
    color: #fff; font-size: 9.5px; font-weight: 600; letter-spacing: .2px;
  }
  .contacts {
    position: absolute; right: 20px; bottom: 58px;
    list-style: none; color: #fff; font-size: 8.6px; text-align: right;
  }
  .contacts li { display: flex; justify-content: flex-end; align-items: center; gap: 6px; height: 15px; }
  .contact-icon {
    width: 10px; height: 10px; border-radius: 50%;
    background: #fff; display: inline-flex; align-items: center; justify-content: center;
  }
</style>
</head>
<body>
  <main class="letterhead">
    <header class="brand">
      <span class="brand-mark"></span>
      <div>
        <div class="brand-name">HALVORSEN</div>
        <div class="brand-sub">Realty Group LLC</div>
      </div>
    </header>

    <article class="letter">
      <p class="date">January 12, 2021</p>
      <p class="recipient">Mr. John Doe<br>President<br>AA Corporation<br>111 Street Name Suite#<br>City, State, 12345</p>
      <p class="salutation">Dear Mr. John,</p>
      <p class="copy">Lorem Ipsum is simply dummy text of the printing and typesetting industry. Lorem Ipsum has been the industry's standard dummy text ever since the 1500s, when an unknown printer took a galley of type and scrambled it to make a type specimen book. It has survived not only five centuries, but also the leap into electronic typesetting, remaining essentially unchanged.</p>
      <p class="copy">The standard chunk of Lorem Ipsum used since the 1500s is reproduced below for those interested. Sections 1.10.32 and 1.10.33 from "de Finibus Bonorum et Malorum" by Cicero are also reproduced in their exact original form, accompanied by English versions from the 1914 translation by H. Rackham.</p>
      <p class="copy">Lorem Ipsum is simply dummy text of the printing and typesetting industry. Lorem Ipsum has been the industry's standard dummy text ever since the 1500s, when an unknown printer took a galley of type and scrambled it to make a type specimen book. It has survived not only five centuries, but also the leap into electronic typesetting, remaining essentially unchanged. It was popularised in the</p>
      <p class="closing">Sincerely Your,</p>
      <div class="signature" role="img" aria-label="Handwritten signature"></div>
    </article>

    <footer class="footer">
      <svg width="534" height="170" viewBox="0 0 534 170" aria-hidden="true">
        <path d="M0 128 L330 128 C360 128 362 96 392 96 L534 96 L534 170 L0 170 Z" fill="var(--grey)"/>
        <path d="M0 138 L330 138 C362 138 360 62 398 56 L534 40 L534 170 L0 170 Z" fill="var(--purple)"/>
      </svg>
      <ul class="contacts">
        <li>(00) 04521 338 760 <span class="contact-icon"><svg width="6" height="6" viewBox="0 0 10 10"><path d="M2 1l2 2-1 1.5c.8 1.5 1.5 2.2 3 3L7.5 6l2 2-1.5 1.5C4.5 9 1 5.5.5 2.5z" fill="var(--purple)"/></svg></span></li>
        <li>(00) 04521 338 761 <span class="contact-icon"><svg width="6" height="6" viewBox="0 0 10 10"><path d="M2 1l2 2-1 1.5c.8 1.5 1.5 2.2 3 3L7.5 6l2 2-1.5 1.5C4.5 9 1 5.5.5 2.5z" fill="var(--purple)"/></svg></span></li>
        <li>hello@halvorsenrealty.com <span class="contact-icon"><svg width="6" height="6" viewBox="0 0 10 10"><rect x="1" y="2" width="8" height="6" fill="none" stroke="var(--purple)" stroke-width="1.2"/><path d="M1 2l4 3.5L9 2" fill="none" stroke="var(--purple)" stroke-width="1.2"/></svg></span></li>
        <li>www.halvorsenrealty.com <span class="contact-icon"><svg width="6" height="6" viewBox="0 0 10 10"><circle cx="5" cy="5" r="4" fill="none" stroke="var(--purple)" stroke-width="1.2"/><path d="M1 5h8M5 1c-2 2.5-2 5.5 0 8M5 1c2 2.5 2 5.5 0 8" fill="none" stroke="var(--purple)" stroke-width="1"/></svg></span></li>
      </ul>
      <p class="office-address">Suite 102 Street name, State, Zip 2024, Country</p>
    </footer>
  </main>
</body>
</html>
```